Heron Dusk business card design

I make handmade colourful women's beaded jewellery (necklaces and earnings).
I require a business card to be designed to truly reflect my jewellery, that is, it is different and stands out.
I would like the business card to look creative, arty, gentle and feminine and fit in with the look of my website and logo (already developed).
I would like the business card to have strong use of the water reeds that are flowing in the wind (please see the banner image on my website www.herondusk.net and attached files).

Target Market(s)

Women who are fashion conscious, hip and funky. My audience like things that are a little different and stand out in a crowd.These women are aged in their 20's-40's.

Industry/Entity Type

Jewelry

Contact Information for Business Card

Please include the following items:
1) my logo: Heron Dusk
2) my name, address and phone number: Darla Fontenot, Sydney, Australia, 0498 315 270
3) my web details: www.herondusk.net, info@herondusk.net, www.facebook.com/herondusk

Font styles to use
Other font styles liked:
• Remachine Script

Requirements
Must have
• My business card must have the following:
• 1) my personal details including all my website contacts (see above).
• 2) Heron Dusk logo
• 3) Reeds flowing in the wind (see my banner image on my website www.herondusk.net or see attached files).
Nice to have
• A sunrise in the background (rising over water)
• I would prefer that the colour scheme to fit with the Heron Dusk logo, that is the colours of an early morning sunrise i.e yellows, oranges. The use of black and white is fine.
Should not have
• I do not like a commercial manufactured look with hard edges. I would like a look that is soft and reflects an artistic, creative and independent business.

```html
<!DOCTYPE html>
<html lang="en">
<head>
<meta charset="utf-8">
<title>Heron Dusk – Business Card</title>
<link rel="stylesheet" href="https://fonts.googleapis.com/css2?family=Courgette&family=Noto+Serif&display=swap">
<style>
  :root {
    --page-bg: #9b9c9c;
    --sun-light: #f2c21b;
    --sun-mid: #eda515;
    --sun-deep: #e2781a;
    --band-dark: #1c1a1b;
    --ink: #1a1718;
    --paper: #e7e7ea;
    --contact-text: #ecebea;
  }
  * { margin: 0; padding: 0; box-sizing: border-box; }
  html, body { width: 1105px; height: 1200px; overflow: hidden; }
  body { background: var(--page-bg); position: relative; }

  .card {
    position: absolute;
    left: 182px;
    width: 748px;
    height: 427px;
    overflow: hidden;
  }
  .card--front { top: 119px; }
  .card--back { top: 637px; background: var(--paper); }

  .sunrise-scene {
    position: absolute;
    left: 0; top: 0;
    width: 100%; height: 278px;
    background:
      linear-gradient(180deg, var(--sun-light) 0%, var(--sun-mid) 55%, var(--sun-deep) 72%, #f0a41e 82%, #f3b62a 100%);
  }

  .brand {
    position: absolute;
    text-align: center;
  }
  .brand__name {
    font-family: "Courgette", cursive;
    font-size: 34px;
    color: var(--ink);
    line-height: 1;
    white-space: nowrap;
  }
  .brand__circle {
    display: block;
    margin: 10px auto 0;
    border: 4px solid var(--ink);
    border-radius: 50%;
  }
  .card--front .brand { left: 52px; top: 40px; width: 200px; }
  .card--front .brand__circle { width: 150px; height: 150px; }
  .card--back .brand { left: 254px; top: 70px; width: 240px; }
  .card--back .brand__name { font-size: 44px; }
  .card--back .brand__circle { width: 206px; height: 206px; }

  .person {
    position: absolute;
    right: 48px;
    top: 38px;
    text-align: right;
    font-family: "Courgette", cursive;
    color: var(--ink);
  }
  .person__name { font-size: 30px; line-height: 1.1; }
  .person__title { font-size: 21px; line-height: 1.3; }

  .contact-band {
    position: absolute;
    left: 0; bottom: 0;
    width: 100%; height: 149px;
    background: var(--band-dark);
    font-family: "Noto Serif", serif;
    font-size: 20px;
    color: var(--contact-text);
  }
  .contact-list {
    position: absolute;
    left: 34px;
    top: 28px;
    list-style: none;
  }
  .contact-list li {
    display: flex;
    align-items: center;
    height: 31px;
  }
  .contact-list svg { width: 20px; height: 20px; margin-right: 14px; flex: none; }
  .location {
    position: absolute;
    right: 48px;
    top: 60px;
    text-align: right;
    line-height: 29px;
  }
</style>
</head>
<body>

  <section class="card card--front" aria-label="Business card front">
    <div class="sunrise-scene" role="img" aria-label="Golden sunrise sky over water with reeds flowing in the wind"></div>

    <div class="brand">
      <div class="brand__name">Heron Dusk</div>
      <span class="brand__circle"></span>
    </div>

    <div class="person">
      <div class="person__name">Ellis Warner</div>
      <div class="person__title">CEO/Founder</div>
    </div>

    <div class="contact-band">
      <ul class="contact-list">
        <li>
          <svg viewBox="0 0 20 20" aria-hidden="true"><path fill="#ecebea" d="M5 2l3 3.5-1.6 2.2c1 2.2 2.7 3.9 4.9 4.9L13.5 11 17 14l-1.8 3.2C9 17 3 11 2.8 3.8z"/></svg>
          0498 315 270
        </li>
        <li>
          <svg viewBox="0 0 20 20" aria-hidden="true"><rect x="2" y="5" width="16" height="11" fill="#ecebea"/><path d="M2.5 5.5l7.5 6 7.5-6" fill="none" stroke="#1c1a1b" stroke-width="1.4"/></svg>
          info@herondusk.net
        </li>
        <li>
          <svg viewBox="0 0 20 20" aria-hidden="true"><circle cx="10" cy="10" r="8" fill="#ecebea"/><path d="M6 6c2 0 2 2 4 2s1 3-1 3-1 3-3 2M12 13c1-1 3-1 3 1" fill="none" stroke="#1c1a1b" stroke-width="1.5"/></svg>
          www.herondusk.net
        </li>
      </ul>
      <div class="location">
        <div>Darla Fontenot</div>
        <div>Sydney, Australia</div>
      </div>
    </div>
  </section>

  <section class="card card--back" aria-label="Business card back">
    <div class="brand">
      <div class="brand__name">Heron Dusk</div>
      <span class="brand__circle"></span>
    </div>
  </section>

</body>
</html>
```